project - Misto Den

Dear designers, I'm Looking for an appealing new business card design to represent us for our new e-cigarette store: The MistO Den. Knowledgeable and friendly staff we aim for superior customer service with a positive atmosphere. Classic feel with modern touch is what we are aiming for . Lime green font and grey back round is the original color scheme but we are flexible and open to suggestions. I added some doodles to show you where my mind is at. address: 4827 203 St SW Edmonton, AB (inside the grand swap bazaar)web: themistoden.com email: info@themistoden.com phone : 555.214.6093 Thanks and am looking forward to seeing your creative , fresh and innovative designs.
Good luck everybody!
Gordon
Updates
lime green and charcoal grey please. thanks
Industry/Entity Type
Business
Logo Text
The MistO Den
Look and feel
Each slider illustrates characteristics of the customer's brand and the style your logo design should communicate.

```html
<!DOCTYPE html>
<html lang="en">
<head>
<meta charset="utf-8">
<title>Misto Den – Business Card</title>
<link rel="stylesheet" href="https://fonts.googleapis.com/css2?family=Exo+2:wght@400;600&display=swap">
<style>
  :root {
    --page-bg: #e4e5e4;
    --card-front: #fbfbfb;
    --card-back: #5f6361;
    --lime: #7dbb3c;
    --charcoal: #3c3f3e;
    --ink: #2e302f;
    --soft-ink: #6b6e6d;
  }
  * { box-sizing: border-box; margin: 0; padding: 0; }
  html, body { width: 1200px; height: 947px; overflow: hidden; }
  body {
    background: var(--page-bg);
    font-family: "Exo 2", sans-serif;
    position: relative;
  }
  .card {
    position: absolute;
    top: 158px;
    width: 360px;
    height: 630px;
    border-radius: 22px;
    box-shadow: 0 6px 18px rgba(0,0,0,0.18);
  }
  .card-back {
    left: 190px;
    background: linear-gradient(160deg, #6a6e6c, var(--card-back) 60%, #555957);
  }
  .social-list {
    position: absolute;
    right: 26px;
    bottom: 26px;
    display: flex;
    gap: 16px;
    list-style: none;
  }
  .social-item {
    display: flex;
    align-items: center;
    gap: 6px;
    color: #d9dcda;
    font-size: 12px;
    letter-spacing: 0.04em;
  }
  .social-square {
    width: 16px; height: 16px;
    background: var(--lime);
    border-radius: 2px;
  }
  .card-front {
    left: 650px;
    background: var(--card-front);
  }
  .brand {
    position: absolute;
    top: 100px;
    left: 0; right: 0;
    display: flex;
    align-items: center;
    justify-content: center;
    gap: 12px;
  }
  .brand-mark {
    width: 18px;
    height: 18px;
    background: var(--lime);
    flex: none;
  }
  .brand-name {
    font-family: "Exo 2", sans-serif;
    font-weight: 600;
    font-size: 34px;
    letter-spacing: 0.08em;
    color: var(--charcoal);
    line-height: 1;
  }
  .info-rows {
    position: absolute;
    top: 240px;
    left: 44px;
    right: 30px;
    list-style: none;
  }
  .info-row {
    display: flex;
    align-items: center;
    height: 66px;
    margin-bottom: 44px;
  }
  .info-icon { width: 40px; height: 40px; flex: none; }
  .info-bar {
    width: 4px;
    height: 46px;
    background: var(--charcoal);
    margin: 0 14px;
    flex: none;
  }
  .info-text {
    font-size: 15px;
    line-height: 1.35;
    color: var(--ink);
    letter-spacing: 0.04em;
    white-space: nowrap;
  }
  .person-name {
    font-weight: 600;
    font-size: 21px;
    color: var(--lime);
    text-transform: uppercase;
    letter-spacing: 0.02em;
    line-height: 1.1;
  }
  .person-role {
    font-size: 12px;
    color: var(--soft-ink);
    letter-spacing: 0.06em;
  }
</style>
</head>
<body>
  <section class="card card-back" aria-label="Card back">
    <ul class="social-list">
      <li class="social-item"><span class="social-square"></span>/chatterly</li>
      <li class="social-item"><span class="social-square"></span>/chirpline</li>
    </ul>
  </section>

  <section class="card card-front" aria-label="Card front">
    <div class="brand">
      <span class="brand-mark" aria-hidden="true"></span>
      <h1 class="brand-name">MISTO DEN</h1>
    </div>
    <ul class="info-rows">
      <li class="info-row">
        <svg class="info-icon" viewBox="0 0 40 40" aria-hidden="true">
          <circle cx="20" cy="12" r="8" fill="var(--lime)"/>
          <path d="M5 37 C5 26 12 22 20 22 C28 22 35 26 35 37 Z" fill="var(--lime)"/>
        </svg>
        <span class="info-bar"></span>
        <div class="info-text">
          <p class="person-name">Owen Hartley</p>
          <p class="person-role">Managing Director</p>
        </div>
      </li>
      <li class="info-row">
        <svg class="info-icon" viewBox="0 0 40 40" aria-hidden="true">
          <path d="M20 2 C12 2 7 8 7 15 C7 25 20 38 20 38 C20 38 33 25 33 15 C33 8 28 2 20 2 Z" fill="var(--lime)"/>
          <circle cx="20" cy="15" r="5" fill="var(--card-front)"/>
        </svg>
        <span class="info-bar"></span>
        <div class="info-text">
          <p>4827 203 St SW</p>
          <p>Edmonton AB</p>
        </div>
      </li>
      <li class="info-row">
        <svg class="info-icon" viewBox="0 0 40 40" aria-hidden="true">
          <circle cx="20" cy="20" r="18" fill="var(--lime)"/>
          <g fill="none" stroke="var(--card-front)" stroke-width="1.8">
            <ellipse cx="20" cy="20" rx="8" ry="17"/>
            <line x1="20" y1="3" x2="20" y2="37"/>
            <line x1="3" y1="20" x2="37" y2="20"/>
            <path d="M6 11 H34 M6 29 H34"/>
          </g>
        </svg>
        <span class="info-bar"></span>
        <div class="info-text">
          <p>555.214.6093</p>
          <p>info@themistoden.com</p>
          <p>themistoden.com</p>
        </div>
      </li>
    </ul>
  </section>
</body>
</html>
```